Business card design for my company.
I would like the card's background colour to be black. You can also see our web site to get an idea of our brand. https://www.tmwhomecrafting.com.au/
- Name
- Email

```html
<!DOCTYPE html>
<html lang="en">
<head>
<meta charset="utf-8">
<title>TMW Home Crafting – Business Card</title>
<link rel="stylesheet" href="https://fonts.googleapis.com/css2?family=Montserrat:wght@400;500;700;800&display=swap">
<style>
  :root {
    --page-bg: #1b1b1b;
    --card-black: #151515;
    --card-white: #f2f2f2;
    --brand-green: #06964a;
    --brand-green-light: #1fa85e;
    --ink: #1c1c1c;
    --white: #ffffff;
  }
  * { box-sizing: border-box; margin: 0; padding: 0; }
  html, body {
    width: 1200px; height: 1059px; overflow: hidden;
    background: var(--page-bg);
    font-family: "Montserrat", sans-serif;
  }
  .card {
    position: absolute;
    border-radius: 22px;
    overflow: hidden;
    box-shadow: 0 10px 28px rgba(0,0,0,.55);
  }
  .card-front {
    left: 256px; top: 89px; width: 689px; height: 393px;
    background: var(--card-white);
  }
  .front-art { position: absolute; inset: 0; }
  .front-brand {
    position: absolute; left: 367px; top: 58px; width: 300px;
    text-align: center; color: var(--white); font-weight: 800;
  }
  .front-brand .brand-initials { display: block; font-size: 82px; line-height: 1; letter-spacing: 4px; }
  .front-brand .brand-words { display: block; font-size: 20px; letter-spacing: 5px; margin-top: 14px; }
  .holder-name {
    position: absolute; left: 24px; top: 208px;
    font-size: 31px; font-weight: 700; color: var(--brand-green);
  }
  .holder-title {
    position: absolute; left: 24px; top: 248px;
    font-size: 17px; font-weight: 500; color: var(--ink); letter-spacing: .3px;
  }
  .contact-list { position: absolute; left: 24px; top: 292px; list-style: none; }
  .contact-list li {
    display: flex; align-items: center; gap: 9px;
    height: 27.5px; font-size: 18px; color: var(--ink); letter-spacing: .2px;
  }
  .contact-list svg { width: 16px; height: 16px; flex: none; }
  .follow {
    position: absolute; right: 26px; top: 279px;
    display: flex; align-items: center; gap: 4px;
    font-size: 17px; color: var(--brand-green); font-weight: 500;
  }
  .follow .label { margin-right: 10px; }
  .social-dot { width: 21px; height: 21px; border-radius: 50%; background: var(--brand-green); }
  .location {
    position: absolute; right: 26px; top: 350px;
    font-size: 18px; color: var(--ink); letter-spacing: .3px;
  }
  .card-back {
    left: 253px; top: 545px; width: 695px; height: 398px;
    background: linear-gradient(120deg, var(--brand-green) 35%, var(--brand-green-light) 60%, var(--brand-green) 85%);
  }
  .back-brand {
    position: absolute; inset: 0;
    display: flex; flex-direction: column; align-items: center; justify-content: center;
    color: var(--white); font-weight: 800;
  }
  .back-brand .brand-initials { font-size: 150px; line-height: 1; letter-spacing: 8px; }
  .back-brand .brand-words { font-size: 34px; letter-spacing: 9px; margin-top: 22px; }
</style>
</head>
<body>

<section class="card card-front">
  <svg class="front-art" viewBox="0 0 689 393" aria-hidden="true">
    <path d="M0 100 C200 205 450 262 689 258 V232 C450 238 230 210 0 100 Z" fill="var(--brand-green)"/>
    <path d="M0 0 H689 V232 C450 240 220 212 0 100 Z" fill="var(--card-black)"/>
    <path d="M0 100 C200 205 450 262 689 258" fill="none" stroke="var(--card-black)" stroke-width="2.5"/>
  </svg>

  <div class="front-brand">
    <span class="brand-initials">TMW</span>
    <span class="brand-words">HOME CRAFTING</span>
  </div>

  <h1 class="holder-name">Liam Hartley</h1>
  <p class="holder-title">General Manager</p>

  <ul class="contact-list">
    <li>
      <svg viewBox="0 0 16 16"><path fill="var(--brand-green)" d="M1 6c0-2 3-3 7-3s7 1 7 3v1h-3V5.5H4V7H1zM4 8h8l2 5H2z"/></svg>
      0412 555 018
    </li>
    <li>
      <svg viewBox="0 0 16 16"><rect x="1" y="4" width="14" height="9" fill="var(--brand-green)"/><path d="M1 4l7 5 7-5" fill="none" stroke="var(--card-white)" stroke-width="1.2"/></svg>
      info@tmwhomecrafting.com.au
    </li>
    <li>
      <svg viewBox="0 0 16 16"><circle cx="8" cy="8" r="7" fill="var(--brand-green)"/><path d="M4 5c2 0 2 2 4 2s0 3 2 4M10 3c0 2 2 2 3 3" fill="none" stroke="var(--card-white)" stroke-width="1.2"/></svg>
      www.tmwhomecrafting.com.au
    </li>
  </ul>

  <div class="follow">
    <span class="label">Follow Us:</span>
    <span class="social-dot"></span>
    <span class="social-dot"></span>
    <span class="social-dot"></span>
  </div>

  <p class="location">Devonport, Tasmania, Australia</p>
</section>

<section class="card card-back">
  <div class="back-brand">
    <span class="brand-initials">TMW</span>
    <span class="brand-words">HOME CRAFTING</span>
  </div>
</section>

</body>
</html>
```